Specialised investor in e-mobility and energy wants business card design

We need a business card design that fits our existing corporate design. <The look and feel must be 'sharp'/'clean', dynamic, communicate momentum, professionalism etc (as one would imagine from a firm in the financial sector). We like the idea of a reverse-side of the card that includes the logo, and the name and contact details on the other. We expect the deliverable to be whatever format might be required to be able to get cards printed directly by a service such as kelmo press. Our website is www.zub.capital

```html
<!DOCTYPE html>
<html lang="en">
<head>
<meta charset="utf-8">
<title>ZUB Capital – Business Card</title>
<link href="https://fonts.googleapis.com/css2?family=Poppins:wght@300;400;600;700&display=swap" rel="stylesheet">
<style>
  :root{
    --brand-green:#2f4d21;
    --paper:#ffffff;
    --ink:#1c1c1c;
    --rule:#9a9a9a;
    --backdrop:#bdbdbd;
  }
  *{margin:0;padding:0;box-sizing:border-box}
  html,body{width:1200px;height:1200px;overflow:hidden}
  body{background:var(--backdrop);font-family:'Poppins',sans-serif;position:relative}
  .card{position:absolute;top:303px;width:368px;height:594px}
  .card--back{left:200px;background:var(--brand-green)}
  .card--front{left:599px;background:var(--paper);color:var(--ink);text-align:center}
  .wordmark{font-family:'Poppins',sans-serif;font-weight:400;white-space:nowrap;position:absolute}
  .card--back .wordmark{left:37px;top:498px;font-size:40px;color:var(--paper)}
  .card--front .wordmark{left:0;right:0;top:118px;font-size:40px;color:var(--brand-green)}
  .person{position:absolute;left:0;right:0;top:332px}
  .person__name{font-size:24px;line-height:1.1;color:var(--brand-green);letter-spacing:.3px}
  .person__name .given{font-weight:700}
  .person__name .family{font-weight:300}
  .person__role{font-size:15.5px;font-weight:400;margin-top:0}
  .contact-icons{position:absolute;left:0;right:0;top:395px;display:flex;justify-content:center;align-items:center;gap:4px}
  .contact-icons .rule{width:52px;height:1px;background:var(--rule);margin:0 4px}
  .contact-icons .icon{width:25px;height:25px;background:var(--brand-green);border-radius:3px;display:flex;align-items:center;justify-content:center}
  .contact{position:absolute;left:0;right:0;top:427px;font-size:16.5px;line-height:21px}
  .divider{position:absolute;left:88px;width:195px;top:506px;height:1px;background:var(--rule)}
  .address{position:absolute;left:0;right:0;top:519px;font-size:16.5px;line-height:21px}
</style>
</head>
<body>
  <section class="card card--back" aria-label="Card reverse">
    <div class="wordmark">ZUB Capital</div>
  </section>

  <section class="card card--front" aria-label="Card front">
    <div class="wordmark">ZUB Capital</div>

    <div class="person">
      <div class="person__name"><span class="given">MARCUS</span> <span class="family">HALE</span></div>
      <div class="person__role">Managing Director</div>
    </div>

    <div class="contact-icons">
      <span class="rule"></span>
      <span class="icon" aria-label="Phone">
        <svg width="15" height="15" viewBox="0 0 16 16"><path d="M2 6c0-2 3-3 6-3s6 1 6 3v1h-3V6H5v1H2z M4 8h8l1 5H3z" fill="#fff"/></svg>
      </span>
      <span class="icon" aria-label="Email">
        <svg width="16" height="12" viewBox="0 0 16 12"><rect x="1" y="1" width="14" height="10" fill="none" stroke="#fff" stroke-width="1.2"/><path d="M1 1l7 6 7-6M1 11l5-5M15 11l-5-5" fill="none" stroke="#fff" stroke-width="1"/></svg>
      </span>
      <span class="icon" aria-label="Website">
        <svg width="16" height="16" viewBox="0 0 16 16"><circle cx="8" cy="8" r="6.5" fill="#fff"/><circle cx="8" cy="8" r="6.5" fill="none" stroke="#fff"/><path d="M5 4c1 1 2 1 2 3s-2 1-2 3M10 5c1 0 2 2 1 3s-1 3-2 3" fill="none" stroke="#2f4d21" stroke-width="1.4"/></svg>
      </span>
      <span class="rule"></span>
    </div>

    <div class="contact">
      <div>044-123 456 789</div>
      <div>info@webname.com</div>
      <div>www.websitename.com</div>
    </div>

    <div class="divider"></div>

    <div class="address">
      <div>421, Address line goes here</div>
      <div>45452,Country Name</div>
    </div>
  </section>
</body>
</html>
```